Now Leasing Banner

Looking for a banner that says the following information approx 4' x 30'

Now Leasing Maplebrook Terrace 925-318-6042

Target Market(s)

Drive by traffic

Industry/Entity Type

Residential property management

Requirements
Must have
• Clear and readable from a distance

```html
<!DOCTYPE html>
<html lang="en">
<head>
<meta charset="utf-8">
<title>Now Leasing Banner – Maplebrook Terrace</title>
<link rel="stylesheet" href="https://fonts.googleapis.com/css2?family=Anton&display=swap">
<style>
  :root {
    --page-bg: #eef0ee;
    --banner-green-light: #5cbf3a;
    --banner-green-mid: #2f9a32;
    --banner-green-dark: #17712a;
    --banner-text: #ffffff;
    --banner-text-shadow: #0f4a1c;
  }

  html, body {
    margin: 0;
    padding: 0;
    width: 1200px;
    height: 800px;
    overflow: hidden;
    background: var(--page-bg);
  }

  .stage {
    width: 1200px;
    height: 800px;
    display: flex;
    align-items: center;
    justify-content: center;
  }

  .leasing-banner {
    display: block;
    width: 1140px;
    height: 152px;
    box-shadow: 0 6px 18px rgba(0, 0, 0, 0.18);
  }

  .banner-headline {
    font-family: "Anton", "Impact", sans-serif;
    font-size: 74px;
    letter-spacing: 1px;
    text-transform: uppercase;
  }

  .banner-headline--shadow { fill: var(--banner-text-shadow); }
  .banner-headline--face   { fill: var(--banner-text); }
</style>
</head>
<body>
  <main class="stage">
    <svg class="leasing-banner" viewBox="0 0 1140 152" role="img"
         aria-label="Now Leasing Maplebrook Terrace 925-318-6042">
      <defs>
        <linearGradient id="banner-fill" x1="0" y1="0" x2="1" y2="1">
          <stop offset="0" stop-color="var(--banner-green-mid)"/>
          <stop offset="0.45" stop-color="var(--banner-green-light)"/>
          <stop offset="1" stop-color="var(--banner-green-dark)"/>
        </linearGradient>
      </defs>

      <rect class="banner-field" width="1140" height="152" fill="url(#banner-fill)"/>

      <text class="banner-headline banner-headline--shadow" x="54" y="106"
            textLength="1040" lengthAdjust="spacingAndGlyphs">Now Leasing Maplebrook Terrace 925-318-6042</text>
      <text class="banner-headline banner-headline--face" x="50" y="102"
            textLength="1040" lengthAdjust="spacingAndGlyphs">Now Leasing Maplebrook Terrace 925-318-6042</text>
    </svg>
  </main>
</body>
</html>
```